Custom Seed Packet design for Flower Farm

We need a design for our seeds packets.
The design will be a kind of "fill in the blanks" as we need the design to be adaptable for multiple varieties of seed. We will be using the design for a rubber stamp.
Our seed packets are 90x90mm in size.
Black logo only. No colour required.
A vintage botanical influence is desired.
Will need to include the following info,
"Wrenfield Gable Co logo" , "Seeds", "Plant Type", "Variety", "Harvested"

```html
<!DOCTYPE html>
<html lang="en">
<head>
<meta charset="utf-8">
<title>Seed Packet – Front and Back</title>
<link rel="stylesheet" href="https://fonts.googleapis.com/css2?family=Playfair+Display:wght@400;600&family=Barlow:wght@600&family=PT+Sans&display=swap">
<style>
  :root {
    --page-bg: #ffffff;
    --label-ink: #111111;
    --stamp-ink: #3a3a3a;
    --kraft-light: #e0c78f;
    --kraft-mid: #d3b574;
    --kraft-edge: #b8924e;
    --faint-art: rgba(255, 255, 255, 0.16);
    --emblem-tone: #b59a63;
  }
  * { margin: 0; padding: 0; box-sizing: border-box; }
  html, body {
    width: 1200px;
    height: 685px;
    overflow: hidden;
    background: var(--page-bg);
  }
  .sheet { position: relative; width: 1200px; height: 685px; }

  .side-label {
    position: absolute;
    top: 42px;
    width: 492px;
    text-align: center;
    font: 400 36px/1 "PT Sans", sans-serif;
    color: var(--label-ink);
  }
  .side-label--front { left: 81px; }
  .side-label--back { left: 626px; }

  .packet {
    position: absolute;
    top: 112px;
    width: 492px;
    height: 492px;
    background:
      radial-gradient(ellipse at 55% 55%, var(--kraft-light) 0%, var(--kraft-mid) 60%, var(--kraft-edge) 100%);
    color: var(--stamp-ink);
    overflow: hidden;
  }
  .packet--front { left: 81px; }
  .packet--back { left: 626px; }

  .packet__frame {
    position: absolute;
    left: 18px;
    top: 18px;
    width: 458px;
    height: 458px;
    border: 3px solid var(--stamp-ink);
  }

  .botanical-backdrop {
    position: absolute;
    background: radial-gradient(ellipse at center, var(--faint-art) 0%, rgba(255,255,255,0) 70%);
  }
  .botanical-backdrop--front { left: 270px; top: 166px; width: 190px; height: 310px; }
  .botanical-backdrop--back { left: 116px; top: 27px; width: 294px; height: 437px; }

  .title-mark { position: absolute; left: 0; top: 0; }
  .title-mark text { fill: var(--stamp-ink); font-family: "Playfair Display", serif; }
  .title-mark__seed { font-weight: 600; font-size: 132px; }
  .title-mark__packet { font-weight: 400; font-size: 19px; }

  .farm-emblem {
    position: absolute;
    left: 150px;
    top: 212px;
    width: 100px;
    height: 100px;
    border-radius: 50%;
    background: radial-gradient(circle at 50% 45%, var(--emblem-tone) 0%, rgba(181,154,99,0.55) 70%, rgba(181,154,99,0) 100%);
  }

  .farm-name {
    position: absolute;
    left: 80px;
    top: 332px;
    width: 332px;
    text-align: center;
    font: 400 24px/1 "Playfair Display", serif;
    color: var(--stamp-ink);
  }

  .write-line {
    position: absolute;
    left: 123px;
    top: 422px;
    width: 286px;
    border-top: 2px solid var(--stamp-ink);
  }

  .info-field { position: absolute; left: 41px; width: 411px; }
  .info-field__label {
    display: block;
    height: 18px;
    font: 600 12.5px/1 "Barlow", sans-serif;
    color: var(--stamp-ink);
  }
  .info-field__box {
    display: block;
    height: 69px;
    border: 1.5px solid var(--stamp-ink);
  }
  .info-field--seeds { top: 45px; }
  .info-field--plant-type { top: 149px; }
  .info-field--variety { top: 254px; }
  .info-field--harvested { top: 358px; }
</style>
</head>
<body>
<main class="sheet">
  <h2 class="side-label side-label--front">Front</h2>
  <h2 class="side-label side-label--back">Back</h2>

  <section class="packet packet--front" aria-label="Seed packet front">
    <div class="botanical-backdrop botanical-backdrop--front" role="img" aria-label="Faint line drawing of poppy stems"></div>
    <div class="packet__frame"></div>
    <svg class="title-mark" width="492" height="200" viewBox="0 0 492 200">
      <text class="title-mark__seed" x="46" y="140" textLength="402" lengthAdjust="spacingAndGlyphs">SEED</text>
      <text class="title-mark__packet" x="126" y="166" textLength="245" lengthAdjust="spacing">PACKET</text>
    </svg>
    <div class="farm-emblem" role="img" aria-label="Farm emblem area"></div>
    <p class="farm-name">Wrenfield Gable Co</p>
    <div class="write-line"></div>
  </section>

  <section class="packet packet--back" aria-label="Seed packet back">
    <div class="botanical-backdrop botanical-backdrop--back" role="img" aria-label="Faint line drawing of poppy bouquet"></div>
    <div class="packet__frame"></div>
    <div class="info-field info-field--seeds">
      <span class="info-field__label">Seeds</span>
      <span class="info-field__box"></span>
    </div>
    <div class="info-field info-field--plant-type">
      <span class="info-field__label">Plant Type</span>
      <span class="info-field__box"></span>
    </div>
    <div class="info-field info-field--variety">
      <span class="info-field__label">Variety</span>
      <span class="info-field__box"></span>
    </div>
    <div class="info-field info-field--harvested">
      <span class="info-field__label">Harvested</span>
      <span class="info-field__box"></span>
    </div>
  </section>
</main>
</body>
</html>
```